HearthMile business card and stationary design

We are looking for a simple yet elegant design for our mortgage company business card and stationary.

The card should include:
Name (Marcus Pell)
Title (CEO)
Phone Number (732-555-0182)
Address (48 Birchwell Court, Suite 314, Larkmoor, WL 01842)
Email (email@hearthmile.example)
"NMLS" i.e. (NMLS 61947)
"Company NMLS" (Company NMLS 274615)

Contact Information for Business Card

See above

```html
<!DOCTYPE html>
<html lang="en">
<head>
<meta charset="utf-8">
<title>HearthMile business card</title>
<link href="https://fonts.googleapis.com/css2?family=Montserrat:wght@500;700&family=Arimo:wght@400&display=swap" rel="stylesheet">
<style>
  :root {
    --stage: #2e3033;
    --navy: #1b2634;
    --navy-deep: #16202c;
    --sky: #0aa3e6;
    --ink: #1b2634;
    --paper: #ffffff;
    --rule: #c9ced4;
  }
  * { margin: 0; padding: 0; box-sizing: border-box; }
  html, body { width: 1200px; height: 1015px; overflow: hidden; background: var(--stage); }
  .canvas {
    width: 1200px; height: 1015px;
    display: flex; flex-direction: column; align-items: center; justify-content: center;
    gap: 56px;
  }
  .card {
    width: 700px; height: 400px; position: relative; overflow: hidden;
    box-shadow: 0 12px 30px rgba(0,0,0,.45);
  }
  /* Back */
  .card-back { background: var(--navy); }
  .card-back .pattern-field {
    position: absolute; inset: 0;
    background: linear-gradient(135deg, #1e2a39 0%, var(--navy-deep) 100%);
  }
  .card-back .brand-name {
    position: absolute; left: 420px; top: 236px;
    font: 700 30px/1 "Montserrat", sans-serif; color: var(--sky); letter-spacing: .5px;
  }
  /* Front */
  .card-front { background: var(--paper); color: var(--ink); }
  .brand-block {
    position: absolute; left: 0; top: 0; width: 340px; height: 318px;
    display: flex; align-items: center; justify-content: center;
  }
  .brand-block .brand-name {
    font: 700 42px/1 "Montserrat", sans-serif; color: var(--ink); letter-spacing: .5px;
  }
  .divider {
    position: absolute; left: 340px; top: 30px; width: 1px; height: 250px;
    background: linear-gradient(to bottom, transparent, var(--rule) 20%, var(--rule) 80%, transparent);
  }
  .contact-block { position: absolute; left: 378px; top: 52px; }
  .person-name { font: 700 32px/1 "Montserrat", sans-serif; color: var(--ink); }
  .person-name .surname { color: var(--sky); }
  .person-title { font: 400 18px/1 "Arimo", sans-serif; margin-top: 6px; }
  .contact-list { list-style: none; margin-top: 22px; }
  .contact-list li {
    display: flex; align-items: center; gap: 9px;
    font: 400 16px/1 "Arimo", sans-serif; margin-bottom: 9px;
  }
  .contact-list svg { width: 15px; height: 15px; flex: none; }
  .contact-list .accent { color: var(--sky); }
  .address { font: 400 16px/1.3 "Arimo", sans-serif; margin-top: 14px; margin-left: 24px; }
  .licence-band {
    position: absolute; left: 0; right: 0; bottom: 0; height: 82px;
    background: var(--navy); border-top: 5px solid var(--sky);
    display: flex; align-items: center; justify-content: center; gap: 14px;
    font: 400 19px/1 "Arimo", sans-serif; color: var(--paper);
  }
  .licence-band .label { color: var(--sky); }
  .licence-band .sep { color: var(--paper); }
</style>
</head>
<body>
<main class="canvas">
  <section class="card card-back" aria-label="Card back">
    <div class="pattern-field" role="img" aria-label="Tone-on-tone embossed repeat of the company name across a dark navy field"></div>
    <div class="brand-name">HearthMile</div>
  </section>

  <section class="card card-front" aria-label="Card front">
    <div class="brand-block"><span class="brand-name">HearthMile</span></div>
    <div class="divider"></div>
    <div class="contact-block">
      <h1 class="person-name">Marcus <span class="surname">Pell</span></h1>
      <p class="person-title">CEO</p>
      <ul class="contact-list">
        <li>
          <svg viewBox="0 0 24 24" aria-hidden="true"><path fill="#0aa3e6" d="M6.6 10.8a15.1 15.1 0 0 0 6.6 6.6l2.2-2.2a1 1 0 0 1 1-.25 11.4 11.4 0 0 0 3.6.57 1 1 0 0 1 1 1V20a1 1 0 0 1-1 1A17 17 0 0 1 3 4a1 1 0 0 1 1-1h3.5a1 1 0 0 1 1 1c0 1.25.2 2.45.57 3.57a1 1 0 0 1-.25 1z"/></svg>
          <span>732-555-0182</span>
        </li>
        <li>
          <svg viewBox="0 0 24 24" aria-hidden="true"><rect x="2" y="5" width="20" height="14" rx="1.5" fill="#0aa3e6"/><path d="M3 6l9 7 9-7" fill="none" stroke="#fff" stroke-width="1.6"/></svg>
          <span>email@hearthmile.example</span>
        </li>
        <li>
          <svg viewBox="0 0 24 24" aria-hidden="true"><g fill="none" stroke="#0aa3e6" stroke-width="2"><circle cx="12" cy="12" r="9.5"/><ellipse cx="12" cy="12" rx="4" ry="9.5"/><path d="M2.5 12h19M4 7h16M4 17h16"/></g></svg>
          <span>www.<span class="accent">hearthmile</span>.example</span>
        </li>
      </ul>
      <p class="address">48 Birchwell Court, Suite 314<br>Larkmoor, WL 01842</p>
    </div>
    <footer class="licence-band">
      <span><span class="label">NMLS</span> 61947</span>
      <span class="sep">|</span>
      <span><span class="label">Company NMLS</span> 274615</span>
    </footer>
  </section>
</main>
</body>
</html>
```